IT Company that provides secure IT solutions and services to our customers

We need business cards and a logo for a new IT Solutions company just created based in Kuala Lumpur, Malaysia. But will also be serving other countries in the region. We provide secure data, voice solutions on mobile platforms. Our first offering is encrypted voice and data solutions for IOS, Android, Windows and BlackBerry devices.

Target Market(s)

large organizations Govt, Police, Defence, Anti-corruption, Legal, highly regulated industries such as Health-care, Financial, Banking, Insurance,

Industry/Entity Type

Information Technology

Contact Information for Business Card

VelmoraNet (Logo - colour is ORVEX blue)Roshan Adeel Managing Director Kryption IT Sdn. Bhd.5th Floor, Block D, Wisma PLB,No.14 Jalan Seri Melor,50470, Kuala LumpurMalaysia

Font styles to use
Sans Serif

Colors
3176b5
ec1f27
fbed22

Requirements
Must have
• VelmoraNet all in Blue like ORVEX blue. A logo design perhaps a play of VN, K with a dangling T (colour can be any)
Nice to have
• I want a clean crisp card, not too busy, easy to read.

```html
<!DOCTYPE html>
<html lang="en">
<head>
<meta charset="utf-8">
<title>VelmoraNet Business Card</title>
<link rel="stylesheet" href="https://fonts.googleapis.com/css2?family=Raleway:wght@500&family=Open+Sans:wght@400;700&display=swap">
<style>
  :root {
    --stage: #000000;
    --card-light: #f3f3f3;
    --brand-blue: #1b5aa8;
    --card-blue: #1c5cab;
    --mark-grey: #444444;
    --ink: #222222;
    --white: #ffffff;
    --ring-faint: rgba(255, 255, 255, 0.07);
  }
  * { margin: 0; padding: 0; box-sizing: border-box; }
  html, body { width: 1200px; height: 900px; overflow: hidden; background: var(--stage); }
  .canvas { position: relative; width: 1200px; height: 900px; background: var(--stage); }

  .card { position: absolute; top: 200px; width: 310px; height: 502px; overflow: hidden; }
  .card-front { left: 265px; background: var(--card-light); border-radius: 70px 0 70px 0; }
  .card-back { left: 641px; background: var(--card-blue); border-radius: 0 70px 0 70px; }

  .brand-dot {
    position: absolute; left: 146px; top: 38px; width: 54px; height: 54px;
    border: 3px solid var(--mark-grey); border-radius: 50%;
  }
  .brand-name {
    position: absolute; font-family: "Raleway", sans-serif; font-weight: 500;
    font-size: 43px; line-height: 1; letter-spacing: 0.2px; white-space: nowrap;
  }
  .card-front .brand-name { left: 63px; top: 102px; color: var(--brand-blue); }
  .card-back .brand-name { left: 48px; top: 400px; color: var(--white); }

  .contact { position: absolute; left: 23px; top: 336px; font-family: "Open Sans", sans-serif; }
  .person-name { font-size: 16px; font-weight: 700; color: var(--brand-blue); line-height: 20px; }
  .person-role { font-size: 13px; color: var(--ink); line-height: 17px; }
  .company-name { margin-top: 32px; font-size: 15px; font-weight: 700; color: var(--brand-blue); line-height: 19px; }
  .company-address { font-size: 13px; color: var(--ink); line-height: 18px; }

  .back-ring { position: absolute; left: 0; top: 0; }
</style>
</head>
<body>
<main class="canvas">
  <section class="card card-front">
    <div class="brand-dot"></div>
    <div class="brand-name">VelmoraNet</div>
    <div class="contact">
      <p class="person-name">Roshan Adeel</p>
      <p class="person-role">Managing Director</p>
      <p class="company-name">Velmora Net</p>
      <p class="company-address">Sdn. Bhd.5th Floor, Block D,&nbsp; Wisma<br>PLB,No.14 Jalan Seri Melor, 50470,<br>Kuala Lumpur Malaysia</p>
    </div>
  </section>

  <section class="card card-back">
    <svg class="back-ring" width="310" height="502" viewBox="0 0 310 502" aria-hidden="true">
      <circle cx="154" cy="200" r="150" fill="none" stroke="var(--ring-faint)" stroke-width="10"/>
    </svg>
    <div class="brand-name">VelmoraNet</div>
  </section>
</main>
</body>
</html>
```